BRTL web site redesign

Coastal Linkage Engineering service (BRTL) is a diverse technology company specialising in design and installation of fibre optics, network convergence and building services, for commercial clients in Australia, we required a new design of our website to attract new clients, generate sales leads, and provide information about our services to the market. The site and should have a new technology look and feel and be designed in word press. our branding colour is blue.

Target Market(s)

New developments, Construction organisations, Commercial end users, IT managers, Consultants.

Industry/Entity Type

It Company

Number of Pages Required

5+ page

Font styles to use
Sans Serif

Colors
0292cd
3176b5

Requirements
Must have
• key pages.
• Home page with some sizzle, automated pictures running through, I like the look of this competitor website http://www.gleamwirex.com.au/ good clean menus and easy to navigate.
• Services page our key services are Fibre optics, Security, Building services,Electrical. I would like the same page layout (Design) for all our services, with a find out more link on each page, manly picture driven with text around our key messaging.
• About us page with space for company profile and directors pictures, bio and contact information.
• Certifications / Accreditations page with have over 20 certifications on different products from suppliers, and a number of licences from governing bodies.
• Current and past projects page with case studies and customer outcomes
• Contact us page with options around what services they require more information on, please keep in mind the site is around generating sales Leeds and being seen as an industry expert.
Nice to have
• RSS feeds, Linked in link, to be placed within the design, Consistent BRTL branding,Same colour blue as our logo Document library for education information, white papers, presentations etc,
• a new technology look and feel, mobile friendly.
Should not have
• boring layout, move away from our cuurent website http://www.brtlgroup.com.au/
• no e eCommerce store required.

```html
<!DOCTYPE html>
<html lang="en">
<head>
<meta charset="utf-8">
<title>BRTL – Coastal Linkage Engineering service</title>
<link href="https://fonts.googleapis.com/css2?family=Oswald:wght@400;500&family=Open+Sans:wght@400;600&display=swap" rel="stylesheet">
<style>
:root{
  --blue:#1a6ea8;
  --blue-dark:#135a8c;
  --brand:#0292cd;
  --ink:#1d1d1d;
  --text:#444;
  --muted:#999;
  --grey-band:#ebebeb;
  --line:#cfcfcf;
  --white:#fff;
}
*{margin:0;padding:0;box-sizing:border-box}
html,body{width:1200px;height:2605px;overflow:hidden;background:var(--white)}
body{font-family:"Open Sans",sans-serif;color:var(--text);position:relative}
.heading{font-family:"Oswald",sans-serif;font-weight:500;text-transform:uppercase}

/* header */
.site-header{position:absolute;top:0;left:0;width:1200px;height:127px;background:var(--white)}
.logo{position:absolute;left:99px;top:38px;display:flex;align-items:center;gap:12px}
.logo-mark{width:40px;height:40px;background:var(--blue)}
.logo-name{font-family:"Oswald",sans-serif;font-weight:500;font-size:40px;color:var(--blue);line-height:1}
.main-nav{position:absolute;top:48px;left:0;width:1200px}
.main-nav a{position:absolute;font-family:"Oswald",sans-serif;font-size:14px;color:#333;text-decoration:none;text-transform:uppercase;white-space:nowrap}
.main-nav a.active::after{content:"";position:absolute;left:-6px;right:-6px;top:28px;height:3px;background:var(--blue)}
.main-nav a.active::before{content:"";position:absolute;left:50%;top:31px;margin-left:-5px;border:5px solid transparent;border-top-color:var(--blue)}

/* hero */
.hero{position:absolute;top:127px;left:0;width:1200px;height:479px;
  background:radial-gradient(ellipse at 25% 30%,#7fb6f0 0%,#2c6fc8 30%,#0d2f78 65%,#061634 100%)}
.hero-card{position:absolute;left:99px;top:55px;width:276px;height:374px;background:rgba(10,14,24,.82);padding:28px 20px 28px 22px}
.hero-card h1{font-size:36px;color:var(--white);line-height:1;margin-bottom:18px;letter-spacing:.5px}
.hero-card p{font-size:13px;line-height:26px;color:#e8e8e8;letter-spacing:-.1px}
.hero-card .more{display:block;margin-top:14px;font-size:13px;color:#e8e8e8;text-decoration:none}
.dots{position:absolute;left:205px;top:332px;display:flex;gap:6px}
.dots span{width:9px;height:9px;border-radius:50%;background:var(--white)}
.dots span:first-child{background:var(--brand)}

/* section headings */
.section-title{position:absolute;left:0;width:1200px;text-align:center}
.section-title h2{font-size:29px;color:var(--ink);line-height:1}
.divider{position:relative;width:184px;height:12px;margin:18px auto 0}
.divider::before{content:"";position:absolute;left:0;right:0;top:6px;height:1px;background:var(--line)}
.divider::after{content:"";position:absolute;left:86px;top:1px;width:10px;height:10px;background:var(--blue);transform:rotate(45deg)}
.lead{position:absolute;left:0;width:1200px;text-align:center;font-size:13px;line-height:23px;color:#333}
.btn{position:absolute;left:526px;width:148px;height:43px;background:var(--blue);color:var(--white);
  font-family:"Oswald",sans-serif;font-size:17px;text-transform:uppercase;display:flex;align-items:center;justify-content:center;text-decoration:none;border:none}

/* services */
.services{position:absolute;top:933px;left:0;width:1200px;height:658px;background:var(--grey-band)}
.service-grid{position:absolute;left:102px;top:147px;width:994px;height:433px;display:grid;grid-template-columns:repeat(4,248.5px);grid-template-rows:216.5px 216.5px}
.service-photo{position:relative}
.photo-fibre{background:radial-gradient(circle at 60% 40%,#6aa6ff 0%,#1f4fc7 40%,#050d3a 100%)}
.photo-security{background:linear-gradient(135deg,#2a3340 0%,#3e6c9a 45%,#1c2229 100%)}
.photo-building{background:linear-gradient(135deg,#c9c2b6 0%,#8a7d6e 50%,#3a342e 100%)}
.photo-electrical{background:linear-gradient(135deg,#e06a22 0%,#c9511a 50%,#6b3a22 100%)}
.service-text{background:var(--white);padding:22px 20px;position:relative}
.service-text h3{font-size:19px;color:var(--blue);line-height:1;margin-bottom:14px}
.service-text p{font-size:13px;line-height:23.5px;color:#333}
.service-text a{display:block;margin-top:10px;font-size:13px;color:var(--blue);text-decoration:none}
.notch-left::before{content:"";position:absolute;left:-9px;top:34px;border:9px solid transparent;border-left:0;border-right-color:var(--white)}
.notch-right::after{content:"";position:absolute;right:-9px;top:34px;border:9px solid transparent;border-right:0;border-left-color:var(--white);z-index:2}

/* contact */
.contact-form .field{position:absolute;left:403px;width:394px;height:40px;border:1px solid #d6d6d6;background:var(--white);
  font-family:"Open Sans",sans-serif;font-size:12.5px;color:var(--muted);padding:0 13px;display:flex;align-items:center}
.contact-form .field.area{height:101px;align-items:flex-start;padding-top:12px}

/* footer */
.site-footer{position:absolute;top:2180px;left:0;width:1200px;height:325px;background:var(--grey-band)}
.footer-col{position:absolute;top:52px}
.footer-col h4{font-size:18px;color:var(--blue);line-height:1;margin-bottom:14px}
.footer-col p,.footer-col li{font-size:13px;line-height:23.5px;color:#333}
.footer-col ul{list-style:none}
.footer-col li{margin-bottom:7px;padding-left:13px;position:relative}
.footer-col li::before{content:"";position:absolute;left:0;top:8px;width:7px;height:7px;border-radius:50%;background:var(--blue)}
.footer-col .link{display:block;margin-top:14px;font-size:13px;color:var(--blue);text-decoration:none}
.blog-item{margin-bottom:18px}
.blog-item strong{display:block;font-weight:600;font-size:13px;color:#222;line-height:23px}
.blog-item time{display:block;font-size:13px;color:var(--blue);line-height:26px}
.bottom-bar{position:absolute;top:2505px;left:0;width:1200px;height:100px;background:var(--blue)}
.bottom-bar p{position:absolute;left:99px;top:40px;font-size:13px;color:var(--white)}
.social{position:absolute;left:937px;top:38px;display:flex;gap:8px}
.social span{width:26px;height:26px;border-radius:50%;background:var(--white)}
</style>
</head>
<body>

<header class="site-header">
  <div class="logo"><span class="logo-mark"></span><span class="logo-name">BRTL</span></div>
  <nav class="main-nav">
    <a class="active" href="#" style="left:474px">Home</a>
    <a href="#" style="left:550px">Services</a>
    <a href="#" style="left:643px">About Us</a>
    <a href="#" style="left:740px">Certifications</a>
    <a href="#" style="left:864px">Current / Past Projects</a>
    <a href="#" style="left:1042px">Contact Us</a>
  </nav>
</header>

<section class="hero" role="img" aria-label="Close-up photograph of glowing blue fibre optic cables plugged into a network switch">
  <div class="hero-card">
    <h1 class="heading">Data &amp; Fibre</h1>
    <p>BRTL has highly trained and proficient engineers, technicians and project managers to ensure that we achieve a high quality Data or Fibre Network, on time and within Budget. Our focus is on delivering quality networks from conception to construction.</p>
    <a class="more" href="#">Read More &gt;&gt;</a>
    <div class="dots"><span></span><span></span><span></span><span></span></div>
  </div>
</section>

<section class="about">
  <div class="section-title" style="top:667px"><h2 class="heading">About Us</h2><div class="divider"></div></div>
  <p class="lead" style="top:738px;padding:0 110px">BRTL is a Communications Integration Company incorporating the expertise of Data and Fibre Optic Communications, ICT and low voltage systems,Security and Application Services. with over five decades of experience and successes in their respected field of expertise. The quality and proven ability of our management and tradespeople, in conjunction with our extensive network of resources, ensures a successful outcome for our clients.</p>
  <a class="btn" href="#" style="top:829px">Read More</a>
</section>

<section class="services">
  <div class="section-title" style="top:59px"><h2 class="heading">Our Services</h2><div class="divider"></div></div>
  <div class="service-grid">
    <div class="service-photo photo-fibre" role="img" aria-label="Photograph of glowing blue fibre optic strands"></div>
    <div class="service-text notch-left">
      <h3 class="heading">Fibre Optics</h3>
      <p>BRTL has highly trained and proficient engineers, technicians and project managers to ensure that we achieve a high quality...</p>
      <a href="#">[ Read More ]</a>
    </div>
    <div class="service-photo photo-security" role="img" aria-label="Photograph of hands working on a fibre splicing machine"></div>
    <div class="service-text notch-left">
      <h3 class="heading">Security</h3>
      <p>BRTL offers a wide range of IP commercial security solutions, from a small standalone system to our fully integrated...</p>
      <a href="#">[ Read More ]</a>
    </div>
    <div class="service-text notch-right">
      <h3 class="heading">Building Services</h3>
      <p>BRTL has highly trained and proficient engineers, technicians and project managers to ensure that we achieve a high quality...</p>
      <a href="#">[ Read More ]</a>
    </div>
    <div class="service-photo photo-building" role="img" aria-label="Photograph of hands wiring a terminal block"></div>
    <div class="service-text notch-right">
      <h3 class="heading">Electrical</h3>
      <p>BRTL offers a wide range of IP commercial security solutions, from a small standalone system to our fully integrated...</p>
      <a href="#">[ Read More ]</a>
    </div>
    <div class="service-photo photo-electrical" role="img" aria-label="Photograph of orange electrical switchboard cabinets"></div>
  </div>
</section>

<section class="contact">
  <div class="section-title" style="top:1655px"><h2 class="heading">Contact Us</h2><div class="divider"></div></div>
  <p class="lead" style="top:1728px;padding:0 140px">We are committed to client satisfaction and strive to implement a comprehensive integrated solution, whilst continually seeking new and innovative ways to improve the capabilities and quality of the services we provide.</p>
  <form class="contact-form">
    <div class="field" style="top:1805px">Name</div>
    <div class="field" style="top:1857px">Email</div>
    <div class="field" style="top:1909px">Phone</div>
    <div class="field area" style="top:1959px">How we can help</div>
    <span class="btn" style="top:2076px">Submit</span>
  </form>
</section>

<footer class="site-footer">
  <div class="footer-col" style="left:99px;width:232px">
    <h4 class="heading">About Us</h4>
    <p>BRTL is diversified technology company 100% Australian owned and operated, we provideCommunication, Electrical, Security &amp; ICT services for residential and commercial customers.</p>
    <a class="link" href="#">[ Read More ]</a>
  </div>
  <div class="footer-col" style="left:406px">
    <h4 class="heading">Services</h4>
    <ul><li>Fibre optics</li><li>Security</li><li>Building services</li><li>Electrical</li></ul>
  </div>
  <div class="footer-col" style="left:606px">
    <h4 class="heading">Information</h4>
    <ul><li>Services</li><li>About us</li><li>Certifications</li><li>Current / Past Projects</li></ul>
  </div>
  <div class="footer-col" style="left:822px;width:280px">
    <h4 class="heading">Latest Blog</h4>
    <div class="blog-item"><strong>Commercial Security Systems</strong><time>22 March 2014</time><p>Lorem ipsum dolor sit amet, vocibus facilis...</p></div>
    <div class="blog-item"><strong>Information Communication &amp; Technology</strong><time>02 April 2014</time><p>Lorem ipsum dolor sit amet, vocibus facilis...</p></div>
  </div>
</footer>

<div class="bottom-bar">
  <p>Copyright @ 2015 BRTL.All Rights Reserved.</p>
  <div class="social" aria-label="Social links"><span></span><span></span><span></span><span></span><span></span></div>
</div>

</body>
</html>
```